Brovanek Data Yellow rose letterhead

I have a new logo for my company but in its current form it is too large to be used on letterhead or as a email signature. I need to have the designer use elements from the current logo and create something close to the original but more suited for smaller items.
Updates

I just uploaded a copy of our logo that does not have the weathered affect. Thanks

Reason: More time for revisions

Industry/Entity Type

It Company

Requirements
Must have
• The design must maintain the visual effect of the current logo. It needs to include the yellow rose and the name of the company.
Nice to have
• It would be nice to maintain the stamp theme and incorporate my name, address, phone, email. etc.

```html
<!DOCTYPE html>
<html lang="en">
<head>
<meta charset="utf-8">
<title>Brovanek Data Letterhead</title>
<link href="https://fonts.googleapis.com/css2?family=Arimo:wght@400;700&display=swap" rel="stylesheet">
<style>
  :root {
    --backdrop: #b5b5b5;
    --paper: #ffffff;
    --band: #584a44;
    --brand-teal: #3bb6b9;
    --accent-yellow: #f5c842;
    --band-text: #ffffff;
    --ink: #4a3a33;
  }
  * { margin: 0; padding: 0; box-sizing: border-box; }
  html, body {
    width: 848px;
    height: 1200px;
    overflow: hidden;
    background: var(--backdrop);
  }
  .letterhead {
    position: absolute;
    left: 108px;
    top: 152px;
    width: 632px;
    height: 895px;
    background: var(--paper);
  }
  .header-band {
    position: absolute;
    left: 0;
    top: 0;
    width: 100%;
    height: 76px;
    background: var(--band);
  }
  .header-rule {
    position: absolute;
    left: 0;
    width: 100%;
  }
  .header-rule--yellow { top: 76px; height: 3px; background: var(--accent-yellow); }
  .header-rule--teal { top: 79px; height: 2px; background: var(--brand-teal); }
  .brand-dot {
    position: absolute;
    left: 16px;
    top: 16px;
    width: 104px;
    height: 104px;
    border-radius: 50%;
    background: var(--accent-yellow);
  }
  .brand-name {
    position: absolute;
    left: 172px;
    top: 20px;
    font-family: "Arimo", sans-serif;
    font-weight: 700;
    font-size: 27px;
    line-height: 1;
    color: var(--brand-teal);
    letter-spacing: 1px;
    white-space: nowrap;
  }
  .header-motto {
    position: absolute;
    left: 172px;
    top: 53px;
    font-family: "Arimo", sans-serif;
    font-size: 15px;
    line-height: 1;
    color: var(--band-text);
    letter-spacing: 3.6px;
    white-space: nowrap;
  }
  .sender-block {
    position: absolute;
    right: 24px;
    top: 782px;
    text-align: right;
    font-family: "Arimo", sans-serif;
    font-size: 13.5px;
    line-height: 18.5px;
    color: var(--ink);
    font-style: normal;
  }
  .sender-name {
    font-weight: 700;
    font-size: 15px;
    line-height: 20px;
  }
</style>
</head>
<body>
  <main class="letterhead">
    <header>
      <div class="header-band"></div>
      <div class="header-rule header-rule--yellow"></div>
      <div class="header-rule header-rule--teal"></div>
      <div class="brand-dot" aria-hidden="true"></div>
      <div class="brand-name">Brovanek Data</div>
      <div class="header-motto">SYSTEMS BUILT TO LAST</div>
    </header>
    <address class="sender-block">
      <div class="sender-name">Marla Kessington, PhD</div>
      <div>418 NE Pecan Ridge Road, Ste 2170</div>
      <div>Dalby Springs, TX 75561</div>
      <div>marla@brovanek-data.com</div>
      <div>1-800-555-0147</div>
    </address>
  </main>
</body>
</html>
```